6 page (for now) squarespace website design for a Mobile Fitness small business

My sons California based small business "BrenVale Coaching" with new subsidiary called "BrenVale 4 Kids". I don't understand coding the website, is that the function squarespace provides?
In the end I want a working website, squarespace, I have a google workspace domain, email and subscription to squarespace & google workspace. URLs include brenvalecoaching.example and brenvale4kids.example. I have an idea of what I am looking for in a website and I have some examples of website designs I like, but I am 100% open to your design concepts and artistic flair. email is torin@brenvalecoaching.example
I am looking for someone to design the site, help me understand how to make "minor" changes and hopefully have a long term relationship on the tech side of the business. I need an Idea of pricing for future changes (Rate T&M).
There are 2 businesses so I need a way to incorporate both the main company and a subsidiary into 1 website or link it somehow. I am open to your suggestions how to accomplish that. Do I need 2 completely separate websites or can it be done on 1 site directing you to different pages. I read conflicting info if it is a BAD idea to link 2 different websites so I will defer to your advice.
Below are the pages I need designed:
- Home Page- BrenVale Coaching
- Home Page- BrenVale 4 Kids (Homeschool market)
- Member Page (subscription service?)
- Workouts- with video clips 1-6 min each
- About
- Contact
- FAQ's
Future work & page designs:
- Store with training subscriptions & a few merch items
- Booking Appointments
- Bookshelf
- email campaign
-Blog
I like the feel of this website:
https://zestlope.example/

```html
<!DOCTYPE html>
<html lang="en">
<head>
<meta charset="utf-8">
<title>BrenVale Coaching</title>
<link rel="stylesheet" href="https://fonts.googleapis.com/css2?family=Poppins:wght@400;500;600;700&family=Mulish:wght@400;600;700;800&display=swap">
<style>
:root{
  --ink:#1d1d1d;
  --body:#444;
  --muted:#777;
  --cream:#f4ebdf;
  --white:#ffffff;
  --line:#cfcfcf;
  --brown:#a07e6b;
  --footer:#f7f7f7;
}
*{box-sizing:border-box;margin:0;padding:0}
html,body{width:1200px;height:5217px;overflow:hidden}
body{font-family:"Mulish",sans-serif;color:var(--ink);background:var(--white);position:relative}
section,header,footer{position:relative;width:1200px}
.abs{position:absolute}
.photo{position:absolute;display:block}
.btn-outline{position:absolute;display:flex;align-items:center;justify-content:center;border:2px solid var(--ink);font:800 14px "Mulish",sans-serif;letter-spacing:.3px;color:var(--ink);background:transparent}
.para{font-size:13.5px;line-height:26px;color:var(--body)}

/* hero */
.hero{height:653px;background:linear-gradient(100deg,#7a4e33 0%,#5a3a28 30%,#2a1e18 60%,#171210 100%);overflow:hidden;color:var(--white)}
.hero .photo{inset:0;background:radial-gradient(ellipse at 28% 40%,rgba(160,120,90,.55),transparent 55%),linear-gradient(180deg,rgba(0,0,0,.15),rgba(0,0,0,.35))}
.brand{position:absolute;display:flex;align-items:center;gap:14px}
.brand .dot{width:44px;height:44px;border-radius:50%;border:3px solid currentColor}
.brand .name{font:500 26px "Poppins",sans-serif;letter-spacing:6px}
.nav{position:absolute;left:474px;top:38px;display:flex}
.nav a{font:400 14px "Mulish",sans-serif;color:var(--white);text-decoration:none;margin-right:34px}
.nav a:last-child{margin-right:0}
.login{position:absolute;left:984px;top:26px;width:104px;height:48px;background:var(--white);color:var(--ink);display:flex;align-items:center;justify-content:center;font:700 15px "Mulish",sans-serif}
.hero .welcome{left:600px;top:210px;font:400 38px "Poppins",sans-serif;letter-spacing:1px}
.hero h1{position:absolute;left:597px;top:262px;font:700 70px "Poppins",sans-serif;letter-spacing:1px;line-height:1}
.hero .lede{left:600px;top:352px;width:440px;font-size:14px;line-height:25px;color:#eee}
.hero-btn{position:absolute;top:428px;height:48px;background:var(--white);color:var(--ink);display:flex;align-items:center;justify-content:center;font:800 14px "Mulish",sans-serif}

/* about */
.about{height:340px}
.about h2{position:absolute;left:111px;top:80px;font:500 30px "Poppins",sans-serif;line-height:46px}
.about .para{position:absolute;left:600px;top:80px;width:488px;text-align:justify}

/* subscriptions */
.subs{height:1717px;background:var(--cream)}
.sec-title{position:absolute;left:0;width:1200px;text-align:center;font:600 29px "Poppins",sans-serif}
.subs .photo{width:489px;height:308px}
.svc h3{position:absolute;font:500 31px "Poppins",sans-serif}
.svc .para{position:absolute;width:420px}

/* faq */
.faq{height:1188px}
.faq-item{position:absolute;left:217px;width:766px;height:80px;border-bottom:1.5px solid var(--line)}
.faq-item span{position:absolute;left:0;top:24px;font:400 14px "Mulish",sans-serif;letter-spacing:.3px;color:#333}
.faq-item svg{position:absolute;right:0;top:25px}
.video{left:111px;top:628px;width:977px;height:473px;border-radius:8px;background:radial-gradient(ellipse at 50% 45%,#6d6660 0%,#3a3733 35%,#1b1d22 75%);overflow:hidden}
.play{position:absolute;left:450px;top:198px;width:78px;height:78px;border-radius:50%;background:var(--white);box-shadow:0 0 0 8px rgba(255,255,255,.35)}

/* blog */
.blog{height:472px;background:var(--cream)}
.blog .kicker{left:111px;top:88px;font:800 13px "Mulish",sans-serif;letter-spacing:.5px}
.blog h2{position:absolute;left:111px;top:114px;font:500 31px "Poppins",sans-serif;line-height:42px}

/* contact */
.contact{height:491px}
.contact h2{position:absolute;left:111px;top:80px;font:500 31px "Poppins",sans-serif}
.label{font:800 14px "Mulish",sans-serif}
.small{font-size:13.5px;color:#555}
.field{position:absolute;height:68px;border:1.5px solid #ccc;border-radius:3px;padding:0 20px;display:flex;align-items:center;font-size:14px;color:#555}
.submit{position:absolute;left:500px;top:355px;width:110px;height:48px;background:var(--brown);color:var(--white);display:flex;align-items:center;justify-content:center;font:800 14px "Mulish",sans-serif}

/* footer */
.site-footer{height:356px;background:var(--footer)}
.col h4{font:500 19px "Poppins",sans-serif;margin-bottom:10px}
.col a{display:block;font-size:14px;line-height:26px;color:#555;text-decoration:none}
.news-input{position:absolute;left:774px;top:115px;width:314px;height:54px;border:1.5px solid #ccc;padding:0 16px;display:flex;align-items:center;font-size:14px;color:#888;background:var(--white)}
.news-btn{position:absolute;left:774px;top:186px;width:126px;height:48px;background:var(--brown);color:var(--white);display:flex;align-items:center;justify-content:center;font:800 14px "Mulish",sans-serif}
.copy{left:111px;top:294px;font-size:14px;color:#333}
</style>
</head>
<body>

<header class="hero">
  <div class="photo" role="img" aria-label="Woman drinking from a red water bottle in a gym with exercise bikes"></div>
  <div class="brand" style="left:111px;top:26px;color:var(--white)"><span class="dot"></span><span class="name">BRENVALE</span></div>
  <nav class="nav">
    <a href="#">Home</a>
    <a href="#">Member</a>
    <a href="#">Workouts</a>
    <a href="#">About</a>
    <a href="#">Contact</a>
    <a href="#">Faq</a>
  </nav>
  <a class="login">log in</a>
  <div class="abs welcome">WELCOME TO</div>
  <h1>BRENVALE</h1>
  <p class="abs lede">Lorem ipsum dolor sit amet, consectetur adipiscing elit, sed do eiusmod tempor incididunt</p>
  <a class="hero-btn" style="left:600px;width:200px">BRENVALE COACHING</a>
  <a class="hero-btn" style="left:812px;width:160px">BRENVALE 4 KIDS</a>
</header>

<section class="about">
  <h2>ABOUT<br>BRENVALE COACHING</h2>
  <a class="btn-outline" style="left:111px;top:205px;width:194px;height:50px">BOOK APPOINTMENT</a>
  <p class="para">Lorem ipsum dolor sit amet, consectetur adipiscing elit, sed do eiusmod tempor incididunt ut labore et dolore magna aliqua. Ut enim ad minim veniam, quis nostrud exercitation ullamco laboris nisi ut aliquip ex ea commodo consequat. Duis aute irure dolor in reprehenderit in voluptate velit esse cillum dolore eu fugiat nulla pariatur. Excepteur sint occaecat cupidatat non proident, sunt in culpa qui officia deserunt mollit anim id est laborum.</p>
</section>

<section class="subs">
  <h2 class="sec-title" style="top:56px">SUBSCRIPTION SERVICE</h2>

  <div class="svc">
    <div class="photo" style="left:111px;top:158px;background:linear-gradient(135deg,#d8d8d8,#8a8a8a 60%,#4a4a4a)" role="img" aria-label="Trainer reviewing a plan on a tablet with a client in a gym"></div>
    <h3 style="left:665px;top:204px">Personal Training</h3>
    <p class="para" style="left:666px;top:254px">Lorem ipsum dolor sit amet, consectetur adipiscing elit, sed do eiusmod tempor incididunt ut labore et dolore magna aliqua.Ut enim ad minim veniam, quis nostrud exercitation ullamco laboris nisi ut aliquip ex ea commodo consequat.</p>
    <a class="btn-outline" style="left:666px;top:377px;width:120px;height:50px">SUBSCRIBE</a>
  </div>

  <div class="svc">
    <div class="photo" style="left:600px;top:552px;background:linear-gradient(120deg,#8fa6b8,#c9c2b4 50%,#9a6a40)" role="img" aria-label="Woman doing a yoga pose in front of a laptop at home"></div>
    <h3 style="left:110px;top:598px">Online Training</h3>
    <p class="para" style="left:111px;top:648px">Lorem ipsum dolor sit amet, consectetur adipiscing elit, sed do eiusmod tempor incididunt ut labore et dolore magna aliqua.Ut enim ad minim veniam, quis nostrud exercitation ullamco laboris nisi ut aliquip ex ea commodo consequat.</p>
    <a class="btn-outline" style="left:111px;top:772px;width:120px;height:50px">SUBSCRIBE</a>
  </div>

  <div class="svc">
    <div class="photo" style="left:111px;top:927px;background:linear-gradient(90deg,#2b2b2b,#6a5a50 45%,#3a3a3a)" role="img" aria-label="Muscular man drinking from a shaker in a gym"></div>
    <h3 style="left:665px;top:972px">Nutritional Guidance</h3>
    <p class="para" style="left:666px;top:1022px">Lorem ipsum dolor sit amet, consectetur adipiscing elit, sed do eiusmod tempor incididunt ut labore et dolore magna aliqua.Ut enim ad minim veniam, quis nostrud exercitation ullamco laboris nisi ut aliquip ex ea commodo consequat.</p>
    <a class="btn-outline" style="left:666px;top:1146px;width:124px;height:50px">SUBSCRIBE</a>
  </div>

  <div class="svc">
    <div class="photo" style="left:600px;top:1322px;background:linear-gradient(160deg,#e6e2da,#9c7a62 55%,#5a4436)" role="img" aria-label="Coach guiding a woman through a lunge in a brick-walled studio"></div>
    <h3 style="left:110px;top:1367px">Business Coaching</h3>
    <p class="para" style="left:111px;top:1417px">Lorem ipsum dolor sit amet, consectetur adipiscing elit, sed do eiusmod tempor incididunt ut labore et dolore magna aliqua.Ut enim ad minim veniam, quis nostrud exercitation ullamco laboris nisi ut aliquip ex ea commodo consequat.</p>
    <a class="btn-outline" style="left:111px;top:1541px;width:127px;height:50px">SUBSCRIBE</a>
  </div>
</section>

<section class="faq">
  <h2 class="sec-title" style="top:82px">FREQUENTLY ASKED QUESTIONS</h2>
  <div class="faq-item" style="top:170px"><span>LOREM IPSUM DOLOR SIT AMET, CONSECTETUR?</span><svg width="16" height="16" viewBox="0 0 16 16"><path d="M8 1v14M1 8h14" stroke="#666" stroke-width="3"/></svg></div>
  <div class="faq-item" style="top:250px"><span>LOREM IPSUM DOLOR SIT AMET, CONSECTETUR?</span><svg width="16" height="16" viewBox="0 0 16 16"><path d="M8 1v14M1 8h14" stroke="#666" stroke-width="3"/></svg></div>
  <div class="faq-item" style="top:330px"><span>LOREM IPSUM DOLOR SIT AMET, CONSECTETUR?</span><svg width="16" height="16" viewBox="0 0 16 16"><path d="M8 1v14M1 8h14" stroke="#666" stroke-width="3"/></svg></div>
  <div class="faq-item" style="top:410px"><span>LOREM IPSUM DOLOR SIT AMET, CONSECTETUR?</span><svg width="16" height="16" viewBox="0 0 16 16"><path d="M8 1v14M1 8h14" stroke="#666" stroke-width="3"/></svg></div>

  <h2 class="sec-title" style="top:548px">WORKOUTS</h2>
  <div class="photo video" role="img" aria-label="Workout video preview of a woman running on a treadmill">
    <div class="play"><svg width="78" height="78" viewBox="0 0 78 78"><path d="M33 28l14 11-14 11z" fill="#111"/></svg></div>
  </div>
</section>

<section class="blog">
  <div class="abs kicker">LATEST BLOG</div>
  <h2>Sed ut perspiciatis<br>omnis iste</h2>
  <p class="para abs" style="left:111px;top:210px;width:420px">Lorem ipsum dolor sit amet, consectetur adipiscing elit, sed do eiusmod tempor incididunt ut labore et dolore magna aliqua.Ut enim ad minim veniam, quis nostrud exercitation ullamco laboris nisi ut aliquip ex ea commodo consequat.</p>
  <a class="btn-outline" style="left:111px;top:336px;width:127px;height:50px">LEARN MORE</a>
  <div class="photo" style="left:600px;top:83px;width:489px;height:308px;background:linear-gradient(90deg,#1c1c1c,#5a5a5a 50%,#222)" role="img" aria-label="Athlete with a jump rope in a dark gym"></div>
</section>

<section class="contact">
  <h2>CONTACT</h2>
  <p class="abs small" style="left:111px;top:152px">Feel free to contact us with any questions.</p>
  <div class="abs label" style="left:111px;top:202px">Email</div>
  <div class="abs small" style="left:111px;top:234px;color:#888">info@brenvalecoaching.example</div>
  <div class="abs label" style="left:111px;top:302px">Phone</div>
  <div class="abs small" style="left:111px;top:334px;color:#888">+1 (555) 014 2280</div>
  <div class="field" style="left:500px;top:87px;width:285px">First Name</div>
  <div class="field" style="left:802px;top:87px;width:286px">Last Name</div>
  <div class="field" style="left:500px;top:177px;width:588px">First Name</div>
  <div class="field" style="left:500px;top:264px;width:588px">First Name</div>
  <a class="submit">SUBMIT</a>
</section>

<footer class="site-footer">
  <div class="brand" style="left:111px;top:68px;color:var(--ink);flex-direction:column;gap:8px;align-items:center;width:120px">
    <span class="dot" style="width:60px;height:60px"></span><span class="name" style="font-size:22px;letter-spacing:5px">BRENVALE</span>
  </div>
  <p class="abs" style="left:111px;top:232px;width:200px;font-size:14px;line-height:25px;color:#333">Lorem ipsum dolor sit amet, adipiscing elit, sed do</p>
  <div class="col abs" style="left:379px;top:70px"><h4>Quick link</h4><a>Home</a><a>Member</a><a>Workouts</a><a>About</a><a>Contact</a><a>Faq</a></div>
  <div class="col abs" style="left:559px;top:70px"><h4>Member</h4><a>Personal Training</a><a>Online Training</a><a>Nutritional Guidance</a><a>Business Coaching</a></div>
  <div class="col abs" style="left:774px;top:70px"><h4>Subscribe To Our Newsletter</h4></div>
  <div class="news-input">Ener Email</div>
  <a class="news-btn">SUBSCRIBE</a>
  <div class="abs copy">©Copyrights 2022 BrenVale Coaching &nbsp;|&nbsp; All Rights Reserved</div>
</footer>

</body>
</html>
```